Whitcombe Business Card Design

The name of the business is Dario Whitcombe, CPA LLC
The service that we offer is Accounting, Tax & Consulting Services. I need it to have the following items:
Dario Whitcombe, Principal
Phone Number
Email Address
Physical Address

I have attached the company logo, one in black and one in white. Please provide a design in black background and the other in white background. Please include "Accounting, Tax & Consulting Services". I want the business card to be clean and very professional.

```html
<!DOCTYPE html>
<html lang="en">
<head>
<meta charset="utf-8">
<title>Dario Whitcombe, CPA LLC — Business Cards</title>
<link rel="stylesheet" href="https://fonts.googleapis.com/css2?family=Montserrat:wght@400;500&family=Roboto+Condensed:wght@400;700&family=Roboto:wght@400&display=swap">
<style>
  :root {
    --page: #e4e4e6;
    --card-dark: #3b3b3d;
    --card-light: #ffffff;
    --frame: #f2f2f2;
    --ink: #3a3a3c;
    --ink-soft: #8a8a8c;
    --accent: #9b1a1d;
    --on-accent: #ffffff;
  }
  * { box-sizing: border-box; margin: 0; padding: 0; }
  html, body { width: 1200px; height: 960px; overflow: hidden; background: var(--page); }
  .canvas { position: relative; width: 1200px; height: 960px; }

  .card {
    position: absolute;
    width: 560px; height: 320px;
    box-shadow: 0 10px 28px rgba(0,0,0,.22);
    overflow: hidden;
  }

  /* Front (dark) */
  .card--front { left: 90px; top: 110px; background: var(--card-dark); }
  .card--front .frame {
    position: absolute; inset: 20px;
    border: 1.5px solid var(--frame);
  }
  .card--front .services {
    position: absolute; left: 50%; bottom: 12px;
    transform: translateX(-50%);
    background: var(--card-dark);
    padding: 0 10px;
    font: 700 12px/16px "Roboto Condensed", sans-serif;
    letter-spacing: .4px;
    color: var(--frame);
    white-space: nowrap;
  }

  .brand { position: absolute; display: flex; align-items: center; gap: 16px; }
  .brand__mark { width: 46px; height: 46px; border: 5px solid currentColor; flex: none; }
  .brand__name {
    font: 400 25px/1 "Montserrat", sans-serif;
    letter-spacing: 1px; text-transform: uppercase; white-space: nowrap;
  }
  .brand__tag {
    margin-top: 6px;
    font: 400 15px/1 "Montserrat", sans-serif;
    letter-spacing: 2.6px; text-transform: uppercase; white-space: nowrap;
  }
  .card--front .brand { left: 70px; top: 128px; color: #d9d9db; }
  .card--front .brand__tag { color: #bdbdbf; }

  /* Back (white) */
  .card--back { left: 550px; top: 530px; background: var(--card-light); }
  .card--back .edge {
    position: absolute; left: 0; top: 118px; bottom: 0; width: 12px;
    background: var(--card-dark);
  }
  .card--back .brand {
    left: 40px; top: 196px; color: var(--ink);
    flex-direction: column; align-items: flex-start; gap: 12px;
  }
  .card--back .brand__name { font-size: 19px; }
  .card--back .brand__tag { font-size: 11.5px; letter-spacing: 2px; color: var(--ink-soft); }
  .card--back .brand__mark { width: 40px; height: 40px; border-width: 4px; align-self: center; }

  .contact {
    position: absolute; left: 290px; right: 0; top: 56px; height: 168px;
    background: var(--accent); color: var(--on-accent);
    padding: 20px 22px 0 26px;
  }
  .contact__name { font: 700 24px/1 "Roboto Condensed", sans-serif; letter-spacing: .6px; text-transform: uppercase; }
  .contact__role { font: 400 14px/1 "Roboto", sans-serif; margin-top: 4px; }
  .contact__list { list-style: none; margin-top: 12px; }
  .contact__list li {
    display: flex; align-items: flex-start; gap: 8px;
    font: 400 12.5px/15px "Roboto", sans-serif; margin-bottom: 3px;
  }
  .contact__list svg { width: 12px; height: 12px; flex: none; margin-top: 2px; fill: var(--on-accent); }
</style>
</head>
<body>
<main class="canvas">

  <section class="card card--front" aria-label="Card front">
    <div class="frame"></div>
    <div class="brand">
      <span class="brand__mark"></span>
      <div>
        <div class="brand__name">Dario Whitcombe, CPA, LLC</div>
        <div class="brand__tag">Certified Public Accountant</div>
      </div>
    </div>
    <p class="services">ACCOUNTING, TAX &amp; CONSULTING SERVICES</p>
  </section>

  <section class="card card--back" aria-label="Card back">
    <div class="edge"></div>
    <div class="brand">
      <span class="brand__mark"></span>
      <div>
        <div class="brand__name">Dario Whitcombe, CPA, LLC</div>
        <div class="brand__tag">Certified Public Accountant</div>
      </div>
    </div>

    <div class="contact">
      <h1 class="contact__name">Dario Whitcombe</h1>
      <p class="contact__role">Principal</p>
      <ul class="contact__list">
        <li>
          <svg viewBox="0 0 24 24" aria-hidden="true"><path d="M12 2a7 7 0 0 0-7 7c0 5 7 13 7 13s7-8 7-13a7 7 0 0 0-7-7zm0 9.5A2.5 2.5 0 1 1 12 6.5a2.5 2.5 0 0 1 0 5z"/></svg>
          <span>4120 Larkspur Court<br>Anchorage, Alaska 99508</span>
        </li>
        <li>
          <svg viewBox="0 0 24 24" aria-hidden="true"><path d="M6.6 10.8a15 15 0 0 0 6.6 6.6l2.2-2.2a1 1 0 0 1 1-.25 11.4 11.4 0 0 0 3.6.57 1 1 0 0 1 1 1V20a1 1 0 0 1-1 1A17 17 0 0 1 3 4a1 1 0 0 1 1-1h3.5a1 1 0 0 1 1 1c0 1.25.2 2.45.57 3.57a1 1 0 0 1-.25 1z"/></svg>
          <span>555-214-0386</span>
        </li>
        <li>
          <svg viewBox="0 0 24 24" aria-hidden="true"><path d="M2 5h20v14H2zm2 2v.5l8 5 8-5V7l-8 5z"/></svg>
          <span>dario@whitcombecpa.com</span>
        </li>
        <li>
          <svg viewBox="0 0 24 24" aria-hidden="true"><circle cx="12" cy="12" r="10"/></svg>
          <span>www.whitcombecpa.com</span>
        </li>
      </ul>
    </div>
  </section>

</main>
</body>
</html>
```